Build a landing page to promote a service (dialler consultation and support).

We are a call centre consultation firm and we need a landing page to promote a service. The service is Tormalux dialler consultation and support.
If you do not know what Tormalux is, please do some quick "Zorvex" research for more information.
The landing page will be promoted with a paid advertisement, so we want something that is simple, and explains exactly what service we offer.
There are two objectives for the landing page:
1) A "call to action" which directs the user to a contact page, including a form plus all of our contact details.
2) A form for them viewers to enter their details to get a "FREE" quote for their project. This form should be placed on the main page.
Notes:
The call to action will require the viewer to enter their name, email, phone number as well as a description of their request. There will also need to be a drop down menu for the type of quote. This menu should have the following options:
1) Tormalux support
2) Tormalux hosting
3) Tormalux customisation
4) Other
We need 2 pages in total:
1) Main landing page
This is the home page. It will need to clearly indicate our services and our key selling features.
Services:
* Tormalux support
* Tormalux hosting
* Tormalux customisation
Key Selling Features:
* Australian based
* PCI complaint
* 10+ years of dialler and call centre experience
* we run a sister company which is a highly reputable 40 seat call centre, so we know first hand about call centre technology.
The main landing page will have an "about us" section with a few paragraphs about how we got started.
-------------------------------------------------------------------------
2) Contact page
All of our contact details will live on this page, as well as a contact form.
Other notes:
We will be self hosting the landing page.
We already have a domain name.
The design must be clean and incorporate our logo, as well as it's colours. (Logo attached)
We want a fully function HTML landing page, not just a "PSD" design.
The page must be mobile optimised.
Anyone using Tormalux software.

```html
<!DOCTYPE html>
<html lang="en">
<head>
<meta charset="utf-8">
<title>Contact Us – Nuvacall</title>
<link rel="stylesheet" href="https://fonts.googleapis.com/css2?family=Varela+Round&family=Poppins:wght@400;500&family=Open+Sans:wght@400&display=swap">
<style>
:root{
  --blue:#1f80c6;
  --green:#26a98b;
  --ink:#111;
  --field:#f5f5f5;
  --field-line:#e6e6e6;
  --white:#fff;
  --muted:#444;
}
*{box-sizing:border-box;margin:0;padding:0}
html,body{width:1114px;height:1200px;overflow:hidden;background:var(--white)}
body{position:relative;font-family:"Poppins",sans-serif;color:var(--ink)}
.abs{position:absolute}
.hero-photo{left:0;top:0;width:1114px;height:312px;
  background:linear-gradient(90deg,#dce9f4 0%,#c5dbee 30%,#e9dfd6 55%,#d7cfc9 75%,#b8ccdf 100%)}
.hero-cut{left:0;top:0}
.brand{left:92px;top:8px;display:flex;align-items:center;gap:8px}
.brand-mark{width:36px;height:36px;border-radius:50%;background:var(--blue)}
.brand-name{font-family:"Varela Round",sans-serif;font-size:22px;color:var(--blue)}
.nav-active{left:441px;top:0;width:56px;height:4px;background:var(--green)}
.nav{left:450px;top:29px;display:flex;gap:0;font-size:13.5px}
.nav a{color:var(--ink);text-decoration:none;margin-right:32px}
.cta{left:886px;top:22px;width:137px;height:38px;background:var(--green);color:var(--white);
  font-size:14px;font-weight:500;display:flex;align-items:center;justify-content:center;border-radius:2px}
.page-title{left:92px;top:150px;font-family:"Varela Round",sans-serif;font-size:55px;color:var(--blue)}
.page-title span{color:var(--green)}
.section-title{left:0;width:1114px;top:386px;text-align:center;font-family:"Varela Round",sans-serif;font-size:36px}
.section-lead{left:0;width:1114px;top:449px;text-align:center;font-size:13px}
.field{background:var(--field);border:1px solid var(--field-line);font-size:10.5px;color:#333;padding:17px 0 0 17px;text-transform:uppercase}
.f-name{left:92px;top:497px;width:318px;height:49px}
.f-email{left:425px;top:497px;width:318px;height:49px}
.f-phone{left:92px;top:561px;width:318px;height:49px}
.f-address{left:425px;top:561px;width:318px;height:49px}
.f-message{left:92px;top:625px;width:651px;height:90px;padding-top:18px}
.submit{left:92px;top:729px;width:132px;height:43px;background:var(--green);color:var(--white);
  font-size:14px;font-weight:500;display:flex;align-items:center;justify-content:center;border-radius:2px}
.agent-photo{left:812px;top:475px;width:222px;height:396px;border-radius:110px 110px 0 0;
  background:linear-gradient(180deg,#e8dcd2 0%,#f2f2f2 45%,#e7e7e7 80%,#333 100%)}
.info-band{left:0;top:871px}
.info{color:var(--white);font-size:13px;line-height:22px}
.info-address{left:150px;top:940px}
.info-phone{left:550px;top:940px}
.info-mail{left:876px;top:940px}
.icon{position:absolute}
.social{left:0;top:1108px;width:1114px;display:flex;justify-content:center;gap:20px}
.social span{width:42px;height:42px;border:1.5px solid var(--green);border-radius:50%}
.legal{left:0;width:1114px;top:1170px;text-align:center;font-family:"Open Sans",sans-serif;font-size:11.5px;color:var(--muted)}
.legal i{font-style:normal;margin:0 8px}
</style>
</head>
<body>

<div class="abs hero-photo" role="img" aria-label="Call centre agents wearing headsets, softly blurred office"></div>
<svg class="abs hero-cut" width="1114" height="312" aria-hidden="true">
  <polygon points="92,280 992,280 1006,312 104,312" fill="#fff"/>
</svg>

<div class="abs brand"><span class="brand-mark"></span><span class="brand-name">Nuvacall</span></div>
<div class="abs nav-active"></div>
<nav class="abs nav">
  <a href="#">Home</a><a href="#">Company</a><a href="#">Services</a><a href="#">Info</a><a href="#">Advantages</a>
</nav>
<div class="abs cta">CONTACT NOW</div>

<h1 class="abs page-title">Contact <span>Us</span></h1>

<h2 class="abs section-title">Let’s Talk With Us</h2>
<p class="abs section-lead">Lorem ipsum dolor sit amet, consectetur adipiscing elit, sed do eiusmod tempor</p>

<div class="abs field f-name">Name</div>
<div class="abs field f-email">Email</div>
<div class="abs field f-phone">Phone No</div>
<div class="abs field f-address">Address</div>
<div class="abs field f-message">Message</div>
<div class="abs submit">SUBMIT</div>

<div class="abs agent-photo" role="img" aria-label="Smiling support agent with headset, arms crossed"></div>

<svg class="abs info-band" width="1114" height="194" aria-hidden="true">
  <rect width="1114" height="194" fill="#1f80c6"/>
  <polygon points="122,163 1022,163 1012,194 108,194" fill="#fff"/>
  <g fill="none" stroke="#fff" stroke-width="1.6">
    <circle cx="114" cy="90" r="20.5"/>
    <circle cx="511" cy="90" r="20.5"/>
    <circle cx="834" cy="90" r="20.5"/>
  </g>
  <path d="M114 80a7 7 0 0 1 7 7c0 5-7 13-7 13s-7-8-7-13a7 7 0 0 1 7-7z" fill="#fff"/>
  <circle cx="114" cy="87" r="2.5" fill="#1f80c6"/>
  <path d="M504 83c1-1 3-1 4 0l2 3c1 1 0 2-1 3l-1 1c1 2 3 4 5 5l1-1c1-1 2-2 3-1l3 2c1 1 1 3 0 4l-1 1c-2 2-6 1-10-3s-6-8-4-11z" fill="#fff"/>
  <rect x="825" y="83" width="18" height="13" rx="2" fill="none" stroke="#fff" stroke-width="1.6"/>
  <path d="M825 85l9 6 9-6" fill="none" stroke="#fff" stroke-width="1.6"/>
</svg>
<div class="abs info info-address">nuvacall call centre consultation firm<br>30418, Australia</div>
<div class="abs info info-phone">Phone :<br>+61 (0) 3/555 018 274</div>
<div class="abs info info-mail">E - Mail :<br>hello@nuvacall.example</div>

<div class="abs social" aria-label="Social links">
  <span role="img" aria-label="Social profile"></span>
  <span role="img" aria-label="Social profile"></span>
  <span role="img" aria-label="Social profile"></span>
  <span role="img" aria-label="Video channel"></span>
  <span role="img" aria-label="Social profile"></span>
</div>

<p class="abs legal">© Copyright Nuvacall 2018<i>|</i>All Rights Reserved<i>|</i>Privacy Policy<i>|</i>Terms Of Use<i>|</i>Faq</p>

</body>
</html>
```